Valdane Companies Business Card Design

We need a new business card for our Private Equity Real Estate Development firm, “Valdane” and our EB-5 regional center “Thornmere Regional Center” on one card. We prefer a design that is simple, elegant, and represents the luxury products we design and build as well as the financial security and stability our successful history has produced. We are an industry leader in our field and 3rd generation family business that has evolved into an institutional quality investment platform. Considered design size is standard business card dimensions (3.5 x 2 inches with an additional 1/8 inch space for design elements or backgrounds that extend beyond the finished size of your piece.

Target Market(s)

• High net worth individuals
• Highly skilled technical workers and physicians in the US seeking investment-based immigration opportunities
• Sophisticated private equity investors
• Intermediary partners include domestic attorneys and investment brokers, as well as international agent networks
• US real estate developers

Industry/Entity Type

Finance

Contact Information for Business Card

(Providing placeholder info for personal information, please design for longer character spaces, longer names and addresses etc..)
• Logo for Valdane
• Logo for Thornmere Regional Center
• Full name: Marcus Valdane
• Job title: CEO
• Email address: mvaldane@valdanecompanies.com
• Cell phone number: +1.555.314.2287
• Office number +1.555.628.4410
• Office address: Larkfield Court 5, 4817 Vista Orilla, Alder Falls, OR.
• Website: www.valdanecompanies.com

Font styles to use
Serif
Sans Serif

Colors
ec1f27
ffffff
000000

Requirements
Must have
• • Logo for Valdane
• • Logo for Thornmere Regional Center
• - Use rounded corners
• (See .ai file included for logos)
Nice to have
• • Simple, elegant design
• • Aesthetically compatible with our website design (www.valdanecompanies.com)
• • Color palette including but not limited to white, black, and red (as per logos)
Should not have
• - Not too much red color
• - Do not stack both logos on top of each other

```html
<!DOCTYPE html>
<html lang="en">
<head>
<meta charset="utf-8">
<title>Valdane Companies Business Card</title>
<link href="https://fonts.googleapis.com/css2?family=Cinzel:wght@600&family=Montserrat:wght@400;500&display=swap" rel="stylesheet">
<style>
  :root {
    --stage: #3a3b3d;
    --card: #060606;
    --panel: #1b1b1c;
    --red: #ec1f27;
    --white: #ffffff;
    --brand-grey: #4a4a4c;
    --name-grey: #3c3c3e;
    --title-grey: #bdbdbd;
    --serif: "Cinzel", Georgia, serif;
    --sans: "Montserrat", Arial, sans-serif;
  }
  * { margin: 0; padding: 0; box-sizing: border-box; }
  html, body { width: 1200px; height: 900px; overflow: hidden; }
  body {
    background: var(--stage);
    display: flex;
    flex-direction: column;
    align-items: center;
    justify-content: center;
    gap: 60px;
  }
  .card {
    position: relative;
    width: 560px;
    height: 320px;
    background: var(--card);
    border-radius: 26px;
    overflow: hidden;
  }

  /* Front */
  .brand {
    position: absolute;
    left: 0; right: 0; top: 0; bottom: 0;
    display: flex;
    align-items: center;
    justify-content: center;
    gap: 18px;
  }
  .brand-square {
    width: 34px; height: 34px;
    background: var(--brand-grey);
  }
  .brand-name {
    font-family: var(--serif);
    font-weight: 600;
    font-size: 44px;
    letter-spacing: 2px;
    color: var(--brand-grey);
  }

  /* Back */
  .panel { position: absolute; top: 0; left: 0; }
  .center-logo {
    position: absolute;
    left: 330px; top: 34px;
    width: 200px;
    display: flex;
    flex-direction: column;
    align-items: center;
    gap: 8px;
  }
  .center-square { width: 30px; height: 30px; background: var(--red); }
  .center-name {
    font-family: var(--serif);
    font-weight: 600;
    color: var(--red);
    text-align: center;
    line-height: 1.1;
  }
  .center-name .line-main { display: block; font-size: 22px; letter-spacing: 1px; }
  .center-name .line-sub { display: block; font-size: 8px; letter-spacing: 4px; margin-top: 3px; }

  .person { position: absolute; left: 46px; top: 132px; }
  .person-name {
    font-family: var(--serif);
    font-weight: 600;
    font-size: 26px;
    line-height: 28px;
    color: var(--name-grey);
  }
  .person-rule {
    width: 56px; height: 1px;
    background: var(--title-grey);
    margin: 10px 0 6px;
  }
  .person-title {
    font-family: var(--sans);
    font-size: 12px;
    letter-spacing: 6px;
    color: var(--title-grey);
  }

  .contacts {
    position: absolute;
    left: 46px; top: 226px;
    list-style: none;
    font-family: var(--sans);
    font-size: 12px;
    line-height: 15px;
    color: var(--white);
  }
  .contact { display: flex; align-items: flex-start; gap: 10px; margin-bottom: 3px; }
  .contact-icon {
    flex: none;
    width: 15px; height: 15px;
    border-radius: 50%;
    background: var(--red);
    display: flex;
    align-items: center;
    justify-content: center;
  }
  .contact-icon svg { width: 9px; height: 9px; }
  .phone-lines { display: grid; grid-template-columns: 46px auto; }
</style>
</head>
<body>

  <section class="card card-front" aria-label="Card front">
    <div class="brand">
      <span class="brand-square"></span>
      <span class="brand-name">VALDANE</span>
    </div>
  </section>

  <section class="card card-back" aria-label="Card back">
    <svg class="panel" width="560" height="320" viewBox="0 0 560 320" aria-hidden="true">
      <path d="M200 0 C240 70 300 112 400 124 Q432 130 448 152 C468 108 515 80 560 74 L560 0 Z" fill="var(--panel)"/>
    </svg>

    <div class="center-logo">
      <span class="center-square"></span>
      <span class="center-name">
        <span class="line-main">THORNMERE</span>
        <span class="line-sub">REGIONAL CENTER</span>
      </span>
    </div>

    <div class="person">
      <p class="person-name">MARCUS<br>VALDANE</p>
      <div class="person-rule"></div>
      <p class="person-title">CEO</p>
    </div>

    <ul class="contacts">
      <li class="contact">
        <span class="contact-icon">
          <svg viewBox="0 0 10 10"><path d="M2 1 L4 1 L4.6 3 L3.5 3.8 Q4.5 5.8 6.2 6.5 L7 5.4 L9 6 L9 8 Q5 9 2.5 6 Q1 4 2 1 Z" fill="var(--white)"/></svg>
        </span>
        <span class="phone-lines">
          <span>Office</span><span>: +1.555.628.4410</span>
          <span>Cell</span><span>: +1.555.314.2287</span>
        </span>
      </li>
      <li class="contact">
        <span class="contact-icon">
          <svg viewBox="0 0 10 10"><rect x="1" y="2.5" width="8" height="5" fill="none" stroke="var(--white)" stroke-width="1"/><path d="M1 2.5 L5 5.5 L9 2.5" fill="none" stroke="var(--white)" stroke-width="1"/></svg>
        </span>
        <span>mvaldane@valdanecompanies.com</span>
      </li>
      <li class="contact">
        <span class="contact-icon">
          <svg viewBox="0 0 10 10"><circle cx="5" cy="5" r="3.8" fill="none" stroke="var(--white)" stroke-width="0.9"/><ellipse cx="5" cy="5" rx="1.6" ry="3.8" fill="none" stroke="var(--white)" stroke-width="0.8"/><path d="M1.2 5 H8.8" stroke="var(--white)" stroke-width="0.8"/></svg>
        </span>
        <span>www.valdanecompanies.com</span>
      </li>
      <li class="contact">
        <span class="contact-icon">
          <svg viewBox="0 0 10 10"><path d="M5 9.5 C3 6.5 2 5 2 3.8 A3 3 0 0 1 8 3.8 C8 5 7 6.5 5 9.5 Z" fill="var(--white)"/><circle cx="5" cy="3.8" r="1.1" fill="var(--red)"/></svg>
        </span>
        <span>Larkfield Court 5, 4817 Vista Orilla, Alder Falls, OR.</span>
      </li>
    </ul>
  </section>

</body>
</html>
```